Business Card Design needed for start up company Halvora

In need of a new business card designed for a start up company based in Sydney, Halvora is a new start up innovative Company, our mission it to make property accessible for everyday Australian and to become the leading Real Estate platform in Australia. We want it to be fresh and clean.

Industry/Entity Type

Financial

Contact Information for Business Card

Section for Name
Section for Title

HALVORA - The Strength of Pooling
Mobile:
Direct:

Font styles to use
Sans Serif

Colors
33a6d7
0692cd
0255a3
ffffff

Requirements
Must have
• Logo, all business card details

```html
<!DOCTYPE html>
<html lang="en">
<head>
<meta charset="utf-8">
<title>Halvora Business Card</title>
<link href="https://fonts.googleapis.com/css2?family=Jost:wght@400;500;700&display=swap" rel="stylesheet">
<style>
  :root {
    --backdrop: #2a2a2a;
    --card-white: #f4f4f4;
    --navy: #213f77;
    --sky: #2a9fd8;
    --ink: #4a4a4a;
    --rule: #8a8a8a;
    --white: #ffffff;
  }
  * { margin: 0; padding: 0; box-sizing: border-box; }
  html, body {
    width: 1200px; height: 960px; overflow: hidden;
    background: var(--backdrop);
    font-family: "Jost", "Futura", sans-serif;
  }
  .stage { position: relative; width: 1200px; height: 960px; }
  .card {
    position: absolute; width: 600px; height: 342px; border-radius: 20px;
  }
  .card-front { left: 302px; top: 124px; background: var(--card-white); }
  .card-back { left: 299px; top: 493px; background: var(--navy); }

  .brand { position: absolute; display: flex; align-items: center; }
  .brand-dot { border-radius: 50%; background: var(--sky); flex: none; }
  .brand-name { font-weight: 700; letter-spacing: -0.5px; line-height: 1; }

  .card-front .brand { right: 30px; top: 42px; }
  .card-front .brand-dot { width: 76px; height: 76px; margin-right: 10px; }
  .card-front .brand-name { font-size: 50px; color: var(--navy); }

  .holder { position: absolute; left: 28px; top: 196px; }
  .holder-name { font-size: 21px; font-weight: 700; color: var(--navy); line-height: 1.1; letter-spacing: 0.3px; }
  .holder-title { font-size: 15px; color: var(--sky); line-height: 1.3; }

  .divider { position: absolute; left: 28px; right: 32px; top: 247px; height: 2px; background: var(--rule); }

  .contacts {
    position: absolute; left: 28px; top: 259px; list-style: none;
    font-size: 14px; color: var(--ink); line-height: 20px;
  }
  .contacts li { display: flex; align-items: center; }
  .contacts svg { width: 14px; height: 14px; margin-right: 8px; fill: var(--navy); flex: none; }

  .address {
    position: absolute; right: 32px; top: 259px; text-align: right;
    font-size: 14px; color: var(--ink); line-height: 20px; font-style: normal;
  }

  .card-back .brand { left: 124px; top: 116px; }
  .card-back .brand-dot { width: 106px; height: 106px; margin-right: 14px; }
  .card-back .brand-name { font-size: 68px; color: var(--white); }

  .tagline {
    position: absolute; left: 0; right: 0; top: 284px; text-align: center;
    font-size: 17px; color: var(--white);
  }
</style>
</head>
<body>
<main class="stage">
  <section class="card card-front" aria-label="Business card front">
    <div class="brand">
      <span class="brand-dot"></span>
      <span class="brand-name">HALVORA</span>
    </div>
    <div class="holder">
      <p class="holder-name">MARCUS DELANE</p>
      <p class="holder-title">CEO/FOUNDER</p>
    </div>
    <div class="divider"></div>
    <ul class="contacts">
      <li>
        <svg viewBox="0 0 24 24" aria-hidden="true"><path d="M6.6 10.8a15.1 15.1 0 0 0 6.6 6.6l2.2-2.2a1 1 0 0 1 1-.25 11.4 11.4 0 0 0 3.6.6 1 1 0 0 1 1 1V20a1 1 0 0 1-1 1A17 17 0 0 1 3 4a1 1 0 0 1 1-1h3.5a1 1 0 0 1 1 1c0 1.25.2 2.45.6 3.6a1 1 0 0 1-.25 1z"/></svg>
        612 480 3917
      </li>
      <li>
        <svg viewBox="0 0 24 24" aria-hidden="true"><path d="M7 1h10a2 2 0 0 1 2 2v18a2 2 0 0 1-2 2H7a2 2 0 0 1-2-2V3a2 2 0 0 1 2-2zm0 3v14h10V4zm5 15.5a1.2 1.2 0 1 0 0 2.4 1.2 1.2 0 0 0 0-2.4z"/></svg>
        704 215 8630
      </li>
      <li>
        <svg viewBox="0 0 24 24" aria-hidden="true"><path d="M2 6h20v12H2zm2 2v.4l8 5 8-5V8l-8 5z"/></svg>
        marcus@halvora.com
      </li>
    </ul>
    <address class="address">
      4123 Harbourview Road<br>
      Sydney, NSW 2000<br>
      www.halvora.com
    </address>
  </section>

  <section class="card card-back" aria-label="Business card back">
    <div class="brand">
      <span class="brand-dot"></span>
      <span class="brand-name">HALVORA</span>
    </div>
    <p class="tagline">The Strength of Pooling</p>
  </section>
</main>
</body>
</html>
```